A4 6 page tri-fold brochure for security screen company

Brochure design and layout for a new company based in the UAE called Harbor Grilles. We make clear mesh security screen doors and windows that aesthetically blend with the house, like a fly screen, rather than a traditional heavy looking security screen. We want to project an image of safety and security but with warmth and humanity to it, not just something clinical. Copy hasn't been written yet so use dummy text or pull and adjust copy form our website www.harborgrilles.ae.
Target market: home owners, financially comfortable, possibly with young children or pets.
Purpose of brochure: to have potential clients contact us (via phone, whatsapp, email or through our website) to arrange a free measure and quote.
More details provided in attached word doc brief and product images, logos etc, attached also.
Please see attached brief.

Target Market(s)

Home owners, financially comfortable, possibly with young children or pets.

Industry/Entity Type

Home Improvement

Font styles to use
Serif
Sans Serif

Colors
0255a3
3176b5
85acd3
cfdfed
eaf1f7

Requirements
Must have
• Good clear images with detailed close ups (or call outs) of specific details such as the mesh and locks.
• Contact details to include website www.harborgrilles.ae, phone number: +971 50 318 2094, email address: oliver@harborgrilles.ae
Nice to have
• If your are comfortable using and adjusting the appropriate copy from our website please do so.
• Images - I've included a lot of images so please choose the most appropriate to help sell the product. Some of the better images I like are: _DSC2929, French_Windows, HARBOR_GRILLES-3204, HARBOR_GRILLES-3231, HARBOR_GRILLES-3345, HARBOR_GRILLES-3354, HARBOR_GRILLES-3401, Girls room windows1, Girls room windows2, IMG_2968. Please don't limit yourself to these images and use the ones you feel best fit.
Should not have
• Please see attached brief.

```html
<!DOCTYPE html>
<html lang="en">
<head>
<meta charset="utf-8">
<title>Harbor Grilles – Brochure Outside</title>
<link rel="stylesheet" href="https://fonts.googleapis.com/css2?family=Montserrat:wght@400;600;700;800&family=Raleway:wght@300;400&family=Roboto:wght@300;400&display=swap">
<style>
  :root{
    --blue-deep:#0255a3;
    --blue-mid:#3176b5;
    --blue-soft:#85acd3;
    --blue-pale:#cfdfed;
    --blue-mist:#eaf1f7;
    --navy:#0b2f63;
    --ink:#222;
    --body:#555;
    --charcoal:#1b1b1d;
    --gold:#e8b53a;
    --stage:#4c4c4e;
    --white:#fff;
  }
  *{margin:0;padding:0;box-sizing:border-box}
  html,body{width:1200px;height:712px;overflow:hidden;background:var(--stage)}
  .brochure{position:absolute;left:20px;top:83px;width:1160px;height:546px;background:var(--white);overflow:hidden;font-family:'Roboto',sans-serif;color:var(--body)}
  .abs{position:absolute}
  .bands{position:absolute;left:0;top:0;width:1160px;height:546px}
  .panel-middle-bg{position:absolute;left:386px;top:0;width:385px;height:546px;background:linear-gradient(180deg,#f3f5f8 0%,#fff 60%)}
  h2.section-title{font-family:'Montserrat',sans-serif;font-weight:400;font-size:14px;color:var(--ink);letter-spacing:.2px}
  h2.section-title strong{font-weight:700;color:var(--blue-deep)}
  .small-copy{font-size:6.6px;line-height:1.5;text-align:justify;color:var(--body)}
  .test-list{list-style:none;font-size:6.6px;line-height:1.6;color:var(--blue-deep)}
  .test-list li::before{content:"•";margin-right:5px}
  .contact-prompt{font-family:'Raleway',sans-serif;font-size:13px;color:var(--blue-deep)}
  .contact-prompt span{display:block;font-family:'Roboto',sans-serif;font-size:7.4px;color:var(--ink)}
  .warranty-title{font-family:'Montserrat',sans-serif;font-weight:700;font-size:14px;color:var(--gold)}
  .gold-rule{width:34px;height:1.5px;background:var(--white)}
  .dark-copy{font-size:6.6px;line-height:1.45;color:#ddd;text-align:justify}
  .web-link{font-family:'Montserrat',sans-serif;font-weight:600;color:var(--white)}
  .center{text-align:center}
  .kicker{font-family:'Montserrat',sans-serif;font-size:9.5px;color:#444;letter-spacing:.2px}
  .headline-blue{font-family:'Montserrat',sans-serif;font-weight:800;font-size:11.6px;line-height:1.4;color:var(--blue-deep)}
  .blue-rule{width:36px;height:1px;background:var(--blue-mid);margin:0 auto}
  .intro{font-size:7.4px;line-height:1.6;color:#444}
  .quote-box{border:1px dashed #b9bec5;border-top:none}
  .quote-mark{font-family:'Montserrat',sans-serif;font-weight:800;font-size:46px;color:#b6b9be;line-height:1}
  .quote-text{font-size:7.6px;line-height:1.6;color:#444}
  .quote-name{font-size:6.8px;color:var(--blue-mid)}
  .quote-name b{color:var(--blue-deep)}
  .brand-name{font-family:'Montserrat',sans-serif;font-weight:700;color:var(--white);letter-spacing:2px;text-align:center}
  .brand-dot{display:inline-block;width:9px;height:9px;background:var(--blue-soft);margin-right:6px;vertical-align:middle}
  .contact-title{font-family:'Montserrat',sans-serif;font-weight:600;font-size:14px;color:var(--white);display:flex;align-items:center;justify-content:center;gap:8px}
  .contact-title::before,.contact-title::after{content:"";width:22px;height:1.5px;background:var(--white)}
  .contact-note{font-size:6.4px;line-height:1.5;color:var(--blue-pale)}
  .contact-phone{font-family:'Montserrat',sans-serif;font-weight:700;font-size:15px;color:var(--white)}
  .contact-line{font-size:9.5px;color:var(--white);display:flex;align-items:center;justify-content:center;gap:5px}
  .cover-title-light{font-family:'Raleway',sans-serif;font-weight:300;font-size:18px;letter-spacing:7px;color:var(--navy)}
  .cover-title-bold{font-family:'Montserrat',sans-serif;font-weight:800;font-size:19px;color:var(--charcoal);letter-spacing:.5px}
  .cover-tagline{font-family:'Montserrat',sans-serif;font-size:13px;line-height:1.35;color:var(--white)}
  .cover-tagline b{font-weight:700}
  .cover-web{font-size:7.4px;letter-spacing:1px;color:#ccc}
</style>
</head>
<body>
<main class="brochure">
  <div class="panel-middle-bg"></div>

  <svg class="bands" viewBox="0 0 1160 546" aria-hidden="true">
    <defs>
      <linearGradient id="dark" x1="0" y1="0" x2="0" y2="1">
        <stop offset="0" stop-color="#2a2a2d"/><stop offset="1" stop-color="#141416"/>
      </linearGradient>
      <linearGradient id="blue" x1="0" y1="0" x2="0" y2="1">
        <stop offset="0" stop-color="#0a3f86"/><stop offset="1" stop-color="#07295b"/>
      </linearGradient>
    </defs>
    <polygon points="0,350 240,350 386,338 386,546 0,546" fill="url(#dark)"/>
    <polygon points="0,362 386,338 386,344 0,368" fill="#3a3a3e" opacity=".8"/>
    <polygon points="386,338 520,350 580,322 640,350 771,338 771,546 386,546" fill="url(#blue)"/>
    <polygon points="386,356 540,372 580,360 620,372 771,356 771,364 620,380 580,368 540,380 386,364" fill="#ffffff" opacity=".85"/>
  </svg>

  <!-- Panel: left -->
  <svg class="abs" style="left:0;top:0" width="175" height="170" role="img" aria-label="Photo: cat sitting at a screened patio door">
    <defs><linearGradient id="catPhoto" x1="0" y1="0" x2="1" y2="1"><stop offset="0" stop-color="#c9d3d8"/><stop offset=".55" stop-color="#eae4da"/><stop offset="1" stop-color="#b38a5c"/></linearGradient></defs>
    <polygon points="0,0 172,0 172,120 130,167 0,167" fill="url(#catPhoto)" stroke="#dfe3e8" stroke-width="3"/>
  </svg>

  <h2 class="section-title abs" style="left:186px;top:10px">PRODUCT <strong>TESTING</strong></h2>
  <p class="small-copy abs" style="left:186px;top:37px;width:178px">All Harbor Grilles products have been designed, manufactured and tested in accordance with strict Australian Security Standards. The screens exceeded the following Australian Security Standards (AS 5039 and 5041) tests:</p>
  <ul class="test-list abs" style="left:190px;top:99px">
    <li>Knife Shear Test</li>
    <li>Dynamic Impact Test</li>
    <li>Lock and Hinge Lever (Jimmy) Test</li>
    <li>Salt Spray Test</li>
  </ul>

  <h2 class="section-title abs" style="left:8px;top:186px">FLY <strong>SCREEN REPAIR</strong></h2>
  <p class="small-copy abs" style="left:11px;top:216px;width:213px">Genuine Harbor Grilles mesh screens are constructed from finely woven stands of stainless steel. The strands are only 0.8mm thick but spaced to ensure flies and mosquitoes can't pass through. A normal fly screen can be cut with a knife, ripped by a cat or pushed in by a child. Harbor Grilles mesh door and window screens pass the Australian Standards 5041 Knife Shear and impact tests. The door and window screens are also resistant to crow bar attack, puncture and tearing.</p>
  <svg class="abs" style="left:234px;top:182px" width="138" height="152" role="img" aria-label="Photo: close-up of stainless steel mesh lit in blue">
    <defs><radialGradient id="meshPhoto" cx=".5" cy=".5" r=".6"><stop offset="0" stop-color="#2f8fe0"/><stop offset=".6" stop-color="#0b3d7a"/><stop offset="1" stop-color="#050f22"/></radialGradient></defs>
    <polygon points="69,3 133,40 133,112 69,149 5,112 5,40" fill="url(#meshPhoto)" stroke="#d9dde2" stroke-width="4"/>
  </svg>
  <p class="contact-prompt abs" style="left:12px;top:308px">Please contact us<span>for a free measure and quote.</span></p>

  <h2 class="warranty-title abs" style="left:12px;top:391px">10 YEAR WARRANTY</h2>
  <div class="gold-rule abs" style="left:13px;top:412px"></div>
  <p class="dark-copy abs" style="left:12px;top:424px;width:235px">Harbor Grilles are manufactured to the highest quality controlled standards by an ISO 9001 certified company. The high tensile, woven, stainless steel mesh has been powdered coated and tested to resist the harsh Middle East elements. With a very small amount of maintenance, your Harbor Grilles will resist the elements and maintain their great look for years to come.</p>
  <p class="dark-copy abs" style="left:12px;top:489px;width:235px">Should you have any problems with your Harbor Grilles, we offer a 10 year warranty on all stainless steel mesh and aluminium products and 1 year on component parts.</p>
  <svg class="abs" style="left:262px;top:410px" width="98" height="98" aria-hidden="true">
    <circle cx="49" cy="49" r="46" fill="var(--gold)"/>
  </svg>
  <p class="web-link abs" style="left:12px;top:526px;font-size:11px">www.harborgrilles.ae</p>

  <!-- Panel: middle -->
  <p class="kicker center abs" style="left:386px;top:11px;width:385px">SUPER STRONG, STAINLESS STEEL MESH</p>
  <h1 class="headline-blue center abs" style="left:386px;top:25px;width:385px">SECURITY SCREENS THAT LOOK STYLISH<br>AND WON'T BREAK.</h1>
  <div class="blue-rule abs" style="left:560px;top:63px"></div>
  <p class="intro center abs" style="left:410px;top:72px;width:340px">Harbor Grilles are a brand new initiative to the UAE. We custom make and install premium high grade stainless steel mesh screen doors and window screens in place of those flimsy fly screens we know drive you crazy.</p>
  <svg class="abs" style="left:386px;top:100px" width="385" height="152" role="img" aria-label="Photos: screened windows and doors in UAE homes">
    <defs>
      <linearGradient id="roomA" x1="0" y1="0" x2="1" y2="1"><stop offset="0" stop-color="#dfe6ee"/><stop offset="1" stop-color="#6d7f92"/></linearGradient>
      <linearGradient id="roomB" x1="0" y1="0" x2="1" y2="1"><stop offset="0" stop-color="#f2f2f0"/><stop offset="1" stop-color="#8d949b"/></linearGradient>
    </defs>
    <g fill="none" stroke="#c5c9cf" stroke-dasharray="2 2"><path d="M0,120 L30,120 M355,125 L385,125"/></g>
    <polygon points="87,8 150,72 87,136 24,72" fill="url(#roomA)" stroke="#fff" stroke-width="3"/>
    <polygon points="167,26 225,84 167,142 109,84" fill="url(#roomB)" stroke="#fff" stroke-width="3"/>
    <polygon points="240,8 296,64 240,120 184,64" fill="url(#roomB)" stroke="#fff" stroke-width="3"/>
    <polygon points="300,52 350,102 300,152 250,102" fill="url(#roomA)" stroke="#fff" stroke-width="3"/>
  </svg>
  <div class="quote-box abs" style="left:423px;top:262px;width:320px;height:56px"></div>
  <p class="quote-mark abs" style="left:440px;top:244px">“</p>
  <p class="quote-text center abs" style="left:428px;top:266px;width:310px">Great product &amp; service. High quality. With this product securing access, allowing fresh air in but keeping the bugs out, I am happy to leave my child's patio door open at night during cool evenings.</p>
  <p class="quote-name abs" style="left:633px;top:306px;background:#fff;padding:0 4px"><b>MARCUS</b> – Palm Grove, Dubai</p>

  <p class="brand-name abs" style="left:386px;top:388px;width:385px;font-size:14px"><span class="brand-dot"></span>HARBOR GRILLES</p>
  <h2 class="contact-title abs" style="left:386px;top:437px;width:385px">CONTACT US</h2>
  <p class="contact-note center abs" style="left:420px;top:460px;width:317px">Please feel free to contact us by completing the email form below or call us if you have any questions or would like to arrange a free measure and quote.</p>
  <p class="contact-phone abs" style="left:386px;top:489px;width:385px;display:flex;justify-content:center;align-items:center;gap:5px">
    <svg width="12" height="12" viewBox="0 0 24 24" aria-hidden="true"><circle cx="12" cy="12" r="10.5" fill="none" stroke="#fff" stroke-width="2"/><path d="M9 7l2 3-1.5 1.5c.8 1.6 1.9 2.7 3.5 3.5L14.5 13l3 2-1 2c-4 0-8.5-4.5-8.5-8.5z" fill="#fff"/></svg>
    +971 50 318 2094</p>
  <p class="contact-line abs" style="left:386px;top:510px;width:385px">
    <svg width="9" height="9" viewBox="0 0 24 24" aria-hidden="true"><circle cx="12" cy="12" r="10" fill="none" stroke="#fff" stroke-width="2.5"/><rect x="6.5" y="8" width="11" height="8" fill="none" stroke="#fff" stroke-width="2"/></svg>
    oliver@harborgrilles.ae</p>
  <p class="contact-line abs" style="left:386px;top:524px;width:385px">
    <svg width="9" height="9" viewBox="0 0 24 24" aria-hidden="true"><circle cx="12" cy="12" r="10" fill="none" stroke="#fff" stroke-width="2.5"/><path d="M2 12h20M12 2c4 4 4 16 0 20M12 2c-4 4-4 16 0 20" fill="none" stroke="#fff" stroke-width="2"/></svg>
    www.harborgrilles.ae</p>

  <!-- Panel: right (cover) -->
  <p class="cover-title-light abs" style="left:771px;top:16px;width:389px;text-align:center">SECURITY SCREEN</p>
  <h1 class="cover-title-bold abs" style="left:771px;top:36px;width:389px;text-align:center">DOORS AND WINDOWS</h1>
  <div class="abs" role="img" aria-label="Photo: young girl looking out through a screened sliding door into the garden" style="left:773px;top:73px;width:387px;height:282px;background:linear-gradient(90deg,#3e8a9a 0%,#a9c7c9 30%,#e9eef0 50%,#c7d8da 75%,#6f9f63 100%)"></div>
  <svg class="bands abs" viewBox="0 0 1160 546" aria-hidden="true" style="left:0;top:0">
    <polygon points="771,352 880,345 967,322 1060,345 1160,356 1160,546 771,546" fill="url(#dark)"/>
    <polygon points="771,362 900,352 967,334 1040,352 1160,368 1160,374 1040,360 967,342 900,360 771,370" fill="#c9ccd1" opacity=".9"/>
  </svg>
  <p class="brand-name abs" style="left:771px;top:400px;width:389px;font-size:17px"><span class="brand-dot"></span>HARBOR GRILLES</p>
  <p class="cover-tagline center abs" style="left:771px;top:462px;width:389px">STRONG SCREENS THAT LET THE<br><b>BREEZE IN AND KEEP INTRUDERS<br>(AND BUGS) OUT!</b></p>
  <p class="cover-web center abs" style="left:771px;top:527px;width:389px">www.harborgrilles.ae</p>
</main>
</body>
</html>
```